BildeVOLD buisnesscard

Hey :) I need a modern buisnesscard for my company BildeVOLD
It most have:
Dagligleder og Fotograf: Henrik Audun Strandvik

Mob: +4791264085
Epost: post@bildevold.example
Adresse: Kvernbakken9, 6040 Langevåg

Facbook and instagram logo with text BildeVOLD

BildeVOLD logo

It Company

```html
<!DOCTYPE html>
<html lang="no">
<head>
<meta charset="utf-8">
<title>BildeVOLD business card</title>
<link href="https://fonts.googleapis.com/css2?family=Open+Sans:wght@400;600;700&display=swap" rel="stylesheet">
<style>
  :root {
    --backdrop: #e4e2df;
    --card-light: #ffffff;
    --card-dark: #232323;
    --ink: #222222;
    --ink-reverse: #ffffff;
    --shadow: rgba(0, 0, 0, 0.28);
  }
  * { box-sizing: border-box; margin: 0; padding: 0; }
  html, body {
    width: 1200px; height: 1000px; overflow: hidden;
    background: var(--backdrop);
    font-family: "Open Sans", Arial, sans-serif;
    color: var(--ink);
  }
  .canvas { position: relative; width: 1200px; height: 1000px; }
  .card {
    position: absolute; left: 266px; width: 666px; height: 397px;
    box-shadow: 0 4px 10px var(--shadow);
  }
  .card-front { top: 74px; background: var(--card-light); }
  .card-back { top: 534px; background: var(--card-dark); }

  .front-brand {
    position: absolute; left: 70px; top: 150px;
    display: flex; align-items: center; gap: 10px;
  }
  .brand-square { width: 18px; height: 18px; background: var(--ink); }
  .brand-name { font-weight: 700; font-size: 36px; letter-spacing: -0.5px; color: var(--ink); }

  .contact { position: absolute; left: 332px; top: 112px; font-size: 16px; line-height: 24px; }
  .contact-name { font-weight: 600; font-size: 18px; letter-spacing: 0.3px; text-transform: uppercase; margin-bottom: 45px; }
  .contact-row { display: flex; align-items: center; gap: 6px; }
  .contact-social { margin-bottom: 10px; }
  .social-mark { width: 11px; height: 11px; background: var(--ink); display: inline-block; }
  .contact-row svg { width: 13px; height: 13px; fill: var(--ink); flex: none; }

  .back-brand {
    position: absolute; left: 0; right: 0; top: 160px;
    text-align: center; font-weight: 700; font-size: 58px;
    color: var(--ink-reverse); letter-spacing: -0.5px;
  }
</style>
</head>
<body>
<main class="canvas">
  <section class="card card-front" aria-label="Business card front">
    <div class="front-brand">
      <span class="brand-square"></span>
      <span class="brand-name">BildeVOLD</span>
    </div>
    <div class="contact">
      <p class="contact-name">Henrik Audun Strandvik</p>
      <p class="contact-row contact-social"><span class="social-mark"></span>BILDEVOLD</p>
      <p class="contact-row">
        <svg viewBox="0 0 24 24" aria-hidden="true"><path d="M6.6 10.8a15.1 15.1 0 0 0 6.6 6.6l2.2-2.2a1 1 0 0 1 1-.25 11.4 11.4 0 0 0 3.6.57 1 1 0 0 1 1 1V20a1 1 0 0 1-1 1A17 17 0 0 1 3 4a1 1 0 0 1 1-1h3.5a1 1 0 0 1 1 1c0 1.25.2 2.45.57 3.6a1 1 0 0 1-.25 1z"/></svg>
        +4791264085
      </p>
      <p class="contact-row">
        <svg viewBox="0 0 24 24" aria-hidden="true"><path d="M2 5h20v2l-10 6L2 7z M2 9l10 6 10-6v10H2z"/></svg>
        post@bildevold.example
      </p>
      <p class="contact-row">Kvernbakken9, 6040 Langevåg.no</p>
    </div>
  </section>

  <section class="card card-back" aria-label="Business card back">
    <p class="back-brand">BildeVOLD</p>
  </section>
</main>
</body>
</html>
```